Business Card for Coastal Tundrabridge Advisory

We need a business card for Coastal Tundrabridge Advisory. The company website address is provided below. The company logo is attached. We provide specialized permafrost services to the mining, transportation, and oil & gas industries. The card should be prepared for:
Matthias Korhonen, PhD.
Coastal Tundrabridge Advisory
PO Box 418259
Quillwater, Alaska 99642
Direct: +1-907-555-0143
Email: mkorhonen@tundrabridgeadvisory.example
Website: www.coastaltundrabridgeadvisory.example

```html
<!DOCTYPE html>
<html lang="en">
<head>
<meta charset="utf-8">
<title>Coastal Tundrabridge Advisory — Business Card</title>
<link rel="stylesheet" href="https://fonts.googleapis.com/css2?family=Open+Sans:wght@300;400;600&family=Roboto+Condensed:wght@400;700&display=swap">
<style>
  :root {
    --backdrop: #2a2a2b;
    --card-navy: #0f1520;
    --card-navy-deep: #0b1019;
    --ink-white: #ffffff;
    --ink-soft: #d9dde3;
    --rule-grey: #8a93a0;
    --ice-blue: #3aa6dc;
    --ice-blue-deep: #1f5f8a;
  }
  * { margin: 0; padding: 0; box-sizing: border-box; }
  html, body {
    width: 1200px; height: 780px; overflow: hidden;
    background: var(--backdrop);
    font-family: "Open Sans", Arial, sans-serif;
    color: var(--ink-white);
  }
  .canvas { position: relative; width: 1200px; height: 780px; }

  .card {
    position: absolute; width: 540px; height: 310px;
    background: var(--card-navy);
    overflow: hidden;
    box-shadow: 0 18px 40px rgba(0,0,0,.45);
  }
  .card--front { left: 40px; top: 235px; }
  .card--back  { left: 620px; top: 235px; }

  /* front */
  .edge-bar { position: absolute; width: 5px; background: var(--ink-white); }
  .edge-bar--left  { left: 0; top: 62px; height: 130px; }
  .edge-bar--right { right: 0; top: 150px; height: 110px; }

  .wordmark {
    font-weight: 600; text-transform: uppercase; color: var(--ink-white);
    letter-spacing: .06em; line-height: 1.2;
  }
  .front-wordmark { position: absolute; left: 36px; top: 58px; font-size: 19px; width: 200px; }

  .divider { position: absolute; left: 0; top: 0; }

  .person { position: absolute; left: 262px; top: 112px; }
  .person-name { font-size: 25px; line-height: 1.1; white-space: nowrap; }
  .person-name .given { font-weight: 600; }
  .person-name .family { font-weight: 300; }
  .person-title { font-size: 15px; font-weight: 400; margin-top: 1px; }

  .contact-list { list-style: none; position: absolute; left: 246px; top: 184px; font-size: 10.5px; color: var(--ink-soft); }
  .contact-list li { display: flex; align-items: center; gap: 6px; height: 15px; white-space: nowrap; }
  .contact-list svg { width: 9px; height: 9px; flex: none; }

  .postal-address { position: absolute; left: 36px; bottom: 26px; font-size: 11.5px; color: var(--ink-soft); }

  /* back */
  .back-pattern {
    position: absolute; inset: 0;
    background: linear-gradient(100deg, var(--card-navy-deep) 0%, var(--card-navy) 45%, var(--ice-blue-deep) 78%, var(--ice-blue) 100%);
  }
  .back-wordmark {
    position: absolute; left: 0; right: 0; top: 92px; text-align: center;
    font-size: 26px;
  }
  .services { position: absolute; left: 30px; bottom: 26px; font-family: "Roboto Condensed", Arial, sans-serif; }
  .services-heading { font-size: 12px; font-weight: 700; letter-spacing: .02em; }
  .services-text { font-size: 11.5px; font-weight: 400; color: var(--ink-soft); margin-top: 3px; }
</style>
</head>
<body>
<main class="canvas">

  <section class="card card--front" aria-label="Business card front">
    <span class="edge-bar edge-bar--left"></span>
    <span class="edge-bar edge-bar--right"></span>

    <div class="wordmark front-wordmark">Coastal Tundrabridge Advisory</div>

    <svg class="divider" width="540" height="310" aria-hidden="true">
      <line x1="150" y1="230" x2="252" y2="100" stroke="var(--rule-grey)" stroke-width="1"/>
    </svg>

    <div class="person">
      <p class="person-name"><span class="given">Matthias</span> <span class="family">Korhonen</span></p>
      <p class="person-title">PhD</p>
    </div>

    <ul class="contact-list">
      <li>
        <svg viewBox="0 0 10 10" aria-hidden="true"><path d="M2 1 L3.6 1 L4.2 3 L3.2 3.8 Q4 5.8 6.2 6.8 L7 5.8 L9 6.4 L9 8 Q9 9 8 9 Q1 8.6 1 2 Q1 1 2 1 Z" fill="var(--ink-white)"/></svg>
        +1-907-555-0143
      </li>
      <li>
        <svg viewBox="0 0 10 10" aria-hidden="true"><rect x="0.6" y="2" width="8.8" height="6" fill="none" stroke="var(--ink-white)" stroke-width="1"/><path d="M0.8 2.3 L5 5.4 L9.2 2.3" fill="none" stroke="var(--ink-white)" stroke-width="1"/></svg>
        mkorhonen@tundrabridgeadvisory.example
      </li>
      <li>
        <svg viewBox="0 0 10 10" aria-hidden="true"><circle cx="5" cy="5" r="4.3" fill="none" stroke="var(--ink-white)" stroke-width="1"/><ellipse cx="5" cy="5" rx="1.9" ry="4.3" fill="none" stroke="var(--ink-white)" stroke-width=".8"/><line x1="0.7" y1="5" x2="9.3" y2="5" stroke="var(--ink-white)" stroke-width=".8"/></svg>
        www.coastaltundrabridgeadvisory.example
      </li>
    </ul>

    <p class="postal-address">PO Box 418259 Quillwater, Alaska 99642</p>
  </section>

  <section class="card card--back" aria-label="Business card back">
    <div class="back-pattern" role="img" aria-label="Repeating company name pattern fading from dark navy to ice blue"></div>
    <div class="wordmark back-wordmark">Coastal Tundrabridge Advisory</div>
    <div class="services">
      <p class="services-heading">OUR SERVICES</p>
      <p class="services-text">We provide specialized permafrost services to the mining, transportation, and oil &amp; gas industries</p>
    </div>
  </section>

</main>
</body>
</html>
```